Brightmill Data Works

Our company is about IT hardwares and IT solutions. IT hardware such as PC, RAMS, storage and servers. IT solutions such as project management, BA. We are also selling new technology too.

Target Market(s)

Consumer, Small to Medium Business, Corporate

Requirements
Must have
• The business card must have the following:
• Name:
• Title:
• Contact Number:
• Email address:
• Website:
• Color: Must match the logo color upgrade

```html
<!DOCTYPE html>
<html lang="en">
<head>
<meta charset="utf-8">
<title>Brightmill Data Works – Business Card</title>
<link href="https://fonts.googleapis.com/css2?family=Lato:wght@400;700;900&display=swap" rel="stylesheet">
<style>
  :root {
    --stage: #3a3a3a;
    --card: #0e0e0f;
    --card-back: #141415;
    --white: #ffffff;
    --orange: #d8741f;
    --orange-band: #c96a22;
    --grey-band: #4a4a4c;
    --muted: #e6e6e6;
  }
  * { margin: 0; padding: 0; box-sizing: border-box; }
  html, body {
    width: 1200px; height: 782px; overflow: hidden;
    background: var(--stage);
    font-family: "Lato", sans-serif;
  }
  .stage {
    position: relative; width: 1200px; height: 782px;
    display: flex; align-items: center; justify-content: center; gap: 40px;
  }
  .card {
    position: relative; width: 540px; height: 309px;
    background: var(--card);
    box-shadow: 0 10px 30px rgba(0,0,0,.45);
    overflow: hidden;
  }
  /* Front */
  .brand {
    position: absolute; left: 36px; top: 54px;
    display: flex; align-items: center; gap: 12px;
  }
  .brand-mark {
    width: 16px; height: 16px; border-radius: 50%;
    background: var(--orange);
  }
  .brand-name {
    font-weight: 900; font-size: 28px; line-height: 1.05;
    color: var(--white); letter-spacing: .5px; text-transform: uppercase;
  }
  .person { position: absolute; left: 36px; top: 150px; }
  .person-name {
    font-size: 19px; font-weight: 400; color: var(--orange);
    text-transform: uppercase; letter-spacing: .3px;
  }
  .person-title { font-size: 14px; color: var(--muted); margin-top: 2px; }
  .contact {
    position: absolute; right: 26px; top: 196px;
    list-style: none; text-align: right;
  }
  .contact li {
    display: flex; align-items: center; justify-content: flex-end; gap: 8px;
    font-size: 15px; color: var(--white); line-height: 20px;
  }
  .contact-icon { width: 13px; height: 13px; flex: none; }
  .card-bands { position: absolute; left: 0; bottom: 0; width: 540px; height: 34px; }
  /* Back */
  .card--back { background: var(--card-back); }
  .back-lockup {
    position: absolute; inset: 0;
    display: flex; flex-direction: column; align-items: center; justify-content: center;
    gap: 22px;
  }
  .back-lockup .brand-name { font-size: 40px; text-align: center; }
  .tagline {
    font-size: 14px; letter-spacing: 1.2px; color: var(--orange);
    text-transform: uppercase;
  }
</style>
</head>
<body>
<main class="stage">
  <section class="card card--front" aria-label="Business card front">
    <div class="brand">
      <span class="brand-mark"></span>
      <span class="brand-name">Brightmill<br>Data Works</span>
    </div>
    <div class="person">
      <p class="person-name">Daniel Harper</p>
      <p class="person-title">Managing Director</p>
    </div>
    <ul class="contact">
      <li>044-987 654 321
        <svg class="contact-icon" viewBox="0 0 16 16"><circle cx="8" cy="8" r="8" fill="var(--orange)"/><path d="M5 4.5l1.6-.5 1 2-1 .8a5 5 0 0 0 2.6 2.6l.8-1 2 1-.5 1.6c-3.4.2-6.7-3.1-6.5-6.5z" fill="var(--card)"/></svg>
      </li>
      <li>info@brightmilldata.com
        <svg class="contact-icon" viewBox="0 0 16 16"><circle cx="8" cy="8" r="8" fill="var(--orange)"/><rect x="4" y="5.2" width="8" height="5.6" fill="var(--card)"/><path d="M4 5.2l4 3 4-3" fill="none" stroke="var(--orange)" stroke-width="1"/></svg>
      </li>
      <li>www.brightmilldata.com
        <svg class="contact-icon" viewBox="0 0 16 16"><circle cx="8" cy="8" r="8" fill="var(--orange)"/><circle cx="8" cy="8" r="4" fill="none" stroke="var(--card)" stroke-width="1.2"/><path d="M4 8h8M8 4c-2 2.5-2 5.5 0 8M8 4c2 2.5 2 5.5 0 8" fill="none" stroke="var(--card)" stroke-width="1"/></svg>
      </li>
    </ul>
    <svg class="card-bands" viewBox="0 0 540 34" preserveAspectRatio="none" aria-hidden="true">
      <polygon points="0,0 300,0 290,34 0,34" fill="var(--grey-band)"/>
      <polygon points="0,12 300,12 290,34 0,34" fill="var(--card)"/>
      <polygon points="312,0 540,0 540,34 300,34" fill="var(--orange-band)"/>
    </svg>
  </section>

  <section class="card card--back" aria-label="Business card back">
    <div class="back-lockup">
      <span class="brand-name">Brightmill Data Works</span>
      <p class="tagline">IT Hardwares and IT Solutions</p>
    </div>
  </section>
</main>
</body>
</html>
```